The Vantor Codex Book Cover

"The Vantor Codex" is a book I wrote with the slogan "Lead With Purpose, Build Momentum: Practical Tools for Teams That Grow Together on Every Screen". The book is designed around a methodology that's mine and that I attached. I would love to see the graphic of the methodology integrated in the design in a very subtle way. Use colors from the model but the book cover should be catchy, modern and engaging to the eye.
Overall the book is about three key elements towards success:
- (Self) Directions (purpose)
- Human experience (people and psychological safety)
- Maximize engagement
The methodology is a FLOW so flow is something that could be incorporated as well in the concept.
Low design quality
Managers and Teams

```html
<!DOCTYPE html>
<html lang="en">
<head>
<meta charset="utf-8">
<title>The Vantor Codex — Book Cover</title>
<link rel="stylesheet" href="https://fonts.googleapis.com/css2?family=Archivo+Black&family=Archivo:wght@500&family=Bebas+Neue&family=Oswald:wght@200;500;700&display=swap">
<style>
  :root {
    --ink: #0d0d0d;
    --paper: #ffffff;
    --mauve: #c95c84;
    --plum: #614a7e;
    --coral: #f26a78;
    --peach: #f5b690;
    --sun: #f3c85a;
    --sky: #4fc1d9;
    --lagoon: #2bbbb0;
    --mint: #a3d9ab;
    --olive: #d5d46a;
  }
  html, body { margin: 0; padding: 0; overflow: hidden; background: var(--paper); }
  .cover {
    position: relative;
    width: 934px;
    height: 1200px;
    overflow: hidden;
    background: var(--paper);
    color: var(--ink);
  }
  .tagline {
    position: absolute;
    top: 62px;
    left: 0;
    width: 934px;
    margin: 0;
    text-align: center;
    font-family: "Oswald", sans-serif;
    font-weight: 500;
    font-size: 16px;
    letter-spacing: 0.42em;
    line-height: 1;
  }
  .title { margin: 0; }
  .title span {
    position: absolute;
    left: 0;
    width: 934px;
    text-align: center;
    line-height: 1;
    white-space: nowrap;
  }
  .title__article {
    top: 102px;
    font-family: "Archivo", sans-serif;
    font-weight: 500;
    font-size: 34px;
    letter-spacing: 0.5em;
    text-transform: uppercase;
  }
  .title__main, .title__second {
    font-family: "Archivo Black", sans-serif;
    font-size: 150px;
    letter-spacing: -2px;
    text-transform: uppercase;
  }
  .title__main { top: 148px; }
  .title__second { top: 296px; }
  .rule {
    position: absolute;
    left: 232px;
    width: 470px;
    height: 3px;
    background: var(--ink);
  }
  .rule--top { top: 470px; }
  .rule--bottom { top: 574px; }
  .subtitle {
    position: absolute;
    top: 484px;
    left: 0;
    width: 934px;
    margin: 0;
    text-align: center;
    font-family: "Bebas Neue", sans-serif;
    font-weight: 400;
    font-size: 38px;
    line-height: 42px;
  }
  .flow-art { position: absolute; left: 0; top: 600px; width: 934px; height: 450px; }
  .author {
    position: absolute;
    top: 1080px;
    left: 0;
    width: 934px;
    margin: 0;
    text-align: center;
    font-family: "Oswald", sans-serif;
    font-size: 54px;
    line-height: 1.2;
    letter-spacing: 0.62em;
  }
  .author__first { font-weight: 200; margin-right: 0.5em; }
  .author__last { font-weight: 700; }
</style>
</head>
<body>
<div class="cover">
  <p class="tagline">LEAD WITH PURPOSE, BUILD MOMENTUM:</p>

  <h1 class="title">
    <span class="title__article">The</span>
    <span class="title__main">Vantor</span>
    <span class="title__second">Codex</span>
  </h1>

  <div class="rule rule--top"></div>
  <p class="subtitle">Practical tools for teams that grow<br>together on every screen</p>
  <div class="rule rule--bottom"></div>

  <svg class="flow-art" viewBox="0 0 934 450" xmlns="http://www.w3.org/2000/svg">
    <defs>
      <linearGradient id="team-tones" x1="0" y1="0" x2="1" y2="0">
        <stop offset="0" stop-color="#d6e4ee"/>
        <stop offset="0.5" stop-color="#c9d6dc"/>
        <stop offset="1" stop-color="#e8e47a"/>
      </linearGradient>
    </defs>

    <rect class="team-photo" x="287" y="30" width="360" height="200" rx="18" fill="url(#team-tones)" role="img" aria-label="Photo of a small team of colleagues standing together"/>

    <g class="flow-ribbon" fill="none" stroke-width="16" stroke-linecap="round">
      <path d="M80 270 C260 200 380 340 467 290 S700 220 854 280" stroke="var(--plum)"/>
      <path d="M80 290 C260 220 380 360 467 310 S700 240 854 300" stroke="var(--mauve)"/>
      <path d="M80 310 C260 240 380 380 467 330 S700 260 854 320" stroke="var(--coral)"/>
      <path d="M80 330 C260 260 380 400 467 350 S700 280 854 340" stroke="var(--peach)"/>
      <path d="M80 350 C260 280 380 420 467 370 S700 300 854 360" stroke="var(--sun)"/>
      <path d="M80 370 C260 300 380 440 467 390 S700 320 854 380" stroke="var(--olive)"/>
      <path d="M80 390 C260 320 380 460 467 410 S700 340 854 400" stroke="var(--mint)"/>
      <path d="M80 410 C260 340 380 480 467 430 S700 360 854 420" stroke="var(--lagoon)"/>
      <path d="M80 430 C260 360 380 500 467 450 S700 380 854 440" stroke="var(--sky)"/>
    </g>
  </svg>

  <p class="author"><span class="author__first">JONAS</span><span class="author__last">VERDIK</span></p>
</div>
</body>
</html>
```